Stationery Design Project

I need a stationary design for our company. we are based in Houston, TX and we are called Mira Vell Lending. And we are wanting to brand our MoneyMendPlus program, which includes our tax preparation and restoration, credit repair service. Although our business offers other programs, we are interested in mainly focusing on The MoneyMendPlus program. We are looking for way to brand our ourselves and I believe that a great stationery design will help in achieving this goal. Our logo design is blue and light blue. the slogan is orange.

Industry/Entity Type

Business

Requirements
Must have
• Address: 30871 Calloway Ln. B-22
Houston, TX 75419
Tel. 555-318-6207
Fax 555-294-7153
www.miravelllending.example
info@miravelllending.example
Our Slogan: Happiness, Restored!

```html
<!DOCTYPE html>
<html lang="en">
<head>
<meta charset="utf-8">
<title>MoneyMendPlus Business Cards</title>
<link rel="stylesheet" href="https://fonts.googleapis.com/css2?family=Tinos:wght@400;700&display=swap">
<style>
  :root {
    --backdrop: #c98a55;
    --card-white: #ffffff;
    --card-edge: #4a3a2c;
    --navy: #143f66;
    --navy-text: #1b4a73;
    --light-blue: #a9cbe6;
    --orange: #f0922b;
    --white: #ffffff;
    --faint-band: rgba(255, 255, 255, 0.06);
    --faint-edge: rgba(255, 255, 255, 0.12);
  }
  * { margin: 0; padding: 0; box-sizing: border-box; }
  html, body {
    width: 1200px;
    height: 702px;
    overflow: hidden;
    background: var(--backdrop);
    font-family: "Tinos", "Times New Roman", serif;
  }
  .sheet { position: relative; width: 1200px; height: 702px; }

  .card {
    position: absolute;
    width: 549px;
    height: 314px;
    border-radius: 22px;
    border: 1px solid var(--card-edge);
    background: var(--card-white);
    text-align: center;
    overflow: hidden;
  }
  .card--front { left: 33px; top: 28px; }
  .card--brand { left: 626px; top: 28px; }
  .card--back  { left: 342px; top: 362px; background: var(--navy); }

  .back-band {
    position: absolute;
    left: 136px; top: 0;
    width: 312px; height: 100%;
    background: var(--faint-band);
    border-left: 1px solid var(--faint-edge);
    border-right: 1px solid var(--faint-edge);
  }

  .mark-dot {
    position: absolute;
    width: 30px; height: 30px;
    border-radius: 50%;
    background: var(--orange);
  }
  .card--front .mark-dot { left: 232px; top: 62px; }
  .card--back .mark-dot { left: 262px; top: 78px; }

  .base-line {
    position: absolute;
    height: 4px;
  }
  .card--front .base-line { left: 127px; width: 296px; top: 136px; background: var(--navy-text); }
  .card--back .base-line { left: 151px; width: 285px; top: 158px; background: var(--white); }

  .program-name {
    position: absolute;
    left: 0; right: 0;
    font-weight: 400;
    font-size: 56px;
    line-height: 1;
    color: var(--navy-text);
  }
  .card--front .program-name { top: 146px; }
  .card--back .program-name { top: 166px; color: var(--white); font-size: 54px; }

  .services {
    position: absolute;
    left: 0; right: 0;
    font-weight: 700;
    font-size: 17.5px;
    color: var(--navy-text);
    letter-spacing: 0.2px;
    white-space: nowrap;
  }
  .card--front .services { top: 229px; }
  .card--brand .services { top: 248px; }
  .services .item { margin: 0 5px; }
  .services .dot {
    display: inline-block;
    width: 7px; height: 7px;
    border-radius: 50%;
    background: var(--orange);
    margin-right: 6px;
    vertical-align: middle;
    position: relative; top: -2px;
  }

  .web {
    position: absolute;
    left: 0; right: 0;
    font-size: 14px;
    letter-spacing: 2.2px;
    color: var(--navy-text);
  }
  .web b { font-weight: 700; }
  .card--front .web { top: 269px; }
  .card--brand .web { top: 276px; }
  .card--back .web { top: 276px; color: var(--white); }

  .slogan {
    position: absolute;
    left: 0; right: 0;
    top: 224px;
    font-size: 15px;
    font-weight: 700;
    color: var(--orange);
  }
  .contact {
    position: absolute;
    left: 0; right: 0;
    font-size: 11.5px;
    color: var(--light-blue);
    letter-spacing: 0.3px;
    white-space: nowrap;
  }
  .contact--address { top: 244px; }
  .contact--lines { top: 258px; }

  .company-square {
    position: absolute;
    left: 177px; top: 24px;
    width: 197px; height: 197px;
    background: var(--navy);
    border: 6px solid var(--light-blue);
    outline: 1px solid var(--navy);
  }
  .company-square .emblem-dot {
    position: absolute;
    left: 50%; top: 46px;
    width: 60px; height: 60px;
    margin-left: -30px;
    border-radius: 50%;
    background: var(--light-blue);
  }
  .company-name {
    position: absolute;
    left: 0; right: 0;
    top: 142px;
    font-size: 16px;
    font-weight: 400;
    color: var(--white);
  }
</style>
</head>
<body>
<main class="sheet">

  <section class="card card--front">
    <span class="mark-dot"></span>
    <span class="base-line"></span>
    <p class="program-name">MoneyMendPlus</p>
    <p class="services">
      <span class="item"><span class="dot"></span>Tax Preparation</span>
      <span class="item"><span class="dot"></span>Restoration</span>
      <span class="item"><span class="dot"></span>Credit Repair Service</span>
    </p>
    <p class="web">www.<b>miravelllending</b>.example</p>
  </section>

  <section class="card card--brand">
    <div class="company-square">
      <span class="emblem-dot"></span>
      <p class="company-name">Mira Vell Lending</p>
    </div>
    <p class="services">
      <span class="item"><span class="dot"></span>Tax Preparation</span>
      <span class="item"><span class="dot"></span>Restoration</span>
      <span class="item"><span class="dot"></span>Credit Repair Service</span>
    </p>
    <p class="web">www.<b>miravelllending</b>.example</p>
  </section>

  <section class="card card--back">
    <span class="back-band"></span>
    <span class="mark-dot"></span>
    <span class="base-line"></span>
    <p class="program-name">MoneyMendPlus</p>
    <p class="slogan">Happiness, Restored!</p>
    <p class="contact contact--address">30871 Calloway Ln. B-22, Houston, TX 75419</p>
    <p class="contact contact--lines">Tel. 555-318-6207 &nbsp;·&nbsp; Fax 555-294-7153 &nbsp;·&nbsp; info@miravelllending.example</p>
    <p class="web">www.<b>miravelllending</b>.example</p>
  </section>

</main>
</body>
</html>
```